Veldmark Supplies Business Card

Professional business card that stand out to our potential customers. Front and back with clean modern design

Industry/Entity Type

Oil and gas

Contact Information for Business Card

Name, address, website , office phone and cell number

Requirements
Must have
• Editable files for each employee

```html
<!DOCTYPE html>
<html lang="en">
<head>
<meta charset="utf-8">
<title>Veldmark Supplies Business Card</title>
<link rel="stylesheet" href="https://fonts.googleapis.com/css2?family=Montserrat:wght@400;500;600;700&display=swap">
<style>
  :root {
    --page-bg: #2b2b2d;
    --brand-blue: #08add0;
    --brand-blue-deep: #0a8fae;
    --brand-red: #ea1c24;
    --ink: #1d1d1f;
    --paper: #ffffff;
  }
  * { box-sizing: border-box; margin: 0; padding: 0; }
  html, body {
    width: 1200px; height: 874px; overflow: hidden;
    background: var(--page-bg);
    font-family: "Montserrat", sans-serif;
  }
  .stage {
    position: relative; width: 1200px; height: 874px;
    display: flex; flex-direction: column; align-items: center; justify-content: center; gap: 40px;
  }
  .card {
    position: relative; width: 560px; height: 320px;
    border-radius: 22px; overflow: hidden;
  }
  /* Back side */
  .card-back {
    background: var(--brand-blue);
    display: flex; align-items: center; justify-content: center;
  }
  .back-wordmark {
    display: flex; align-items: center; gap: 14px;
    color: var(--brand-blue-deep);
    font-weight: 700; font-size: 34px; letter-spacing: 2px; text-transform: uppercase;
  }
  .back-wordmark .mark-square {
    width: 30px; height: 30px; background: var(--brand-blue-deep);
  }
  /* Front side */
  .card-front { background: var(--paper); }
  .front-band {
    position: absolute; left: 0; right: 0; top: 222px; height: 70px;
    background: var(--brand-blue);
  }
  .logo-area {
    position: absolute; left: 0; top: 48px; width: 258px; height: 172px;
    display: flex; align-items: center; justify-content: center;
  }
  .front-wordmark {
    display: flex; align-items: center; gap: 8px; white-space: nowrap;
    color: var(--brand-red); font-weight: 700; font-size: 15px; letter-spacing: .5px; text-transform: uppercase;
  }
  .front-wordmark .mark-square { width: 15px; height: 15px; background: var(--brand-red); flex: none; }
  .divider {
    position: absolute; left: 258px; top: 48px; width: 2px; height: 172px;
    background: var(--brand-red);
  }
  .person { position: absolute; left: 276px; top: 50px; }
  .person-name { color: var(--brand-red); font-weight: 700; font-size: 24px; line-height: 1.1; }
  .person-title { color: var(--ink); font-size: 13px; margin-top: 2px; }
  .contacts {
    position: absolute; left: 276px; top: 112px;
    list-style: none; display: flex; flex-direction: column; gap: 6px;
  }
  .contact-item {
    display: flex; align-items: center; gap: 9px;
    color: var(--ink); font-size: 13.5px; font-weight: 500;
  }
  .contact-icon { width: 13px; height: 13px; flex: none; }
  .address {
    position: absolute; left: 0; right: 0; top: 246px;
    text-align: center; color: var(--paper); font-size: 14px; font-weight: 500; letter-spacing: .3px;
  }
</style>
</head>
<body>
<main class="stage">
  <section class="card card-back" aria-label="Card back">
    <div class="back-wordmark"><span class="mark-square"></span>Veldmark Supplies</div>
  </section>

  <section class="card card-front" aria-label="Card front">
    <div class="front-band"></div>
    <div class="logo-area">
      <div class="front-wordmark"><span class="mark-square"></span>Veldmark Supplies</div>
    </div>
    <div class="divider"></div>
    <div class="person">
      <p class="person-name">Karim Soltani</p>
      <p class="person-title">President</p>
    </div>
    <ul class="contacts">
      <li class="contact-item">
        <svg class="contact-icon" viewBox="0 0 16 16"><path fill="#08add0" d="M2 5c0-2 2-3 6-3s6 1 6 3v1h-3V4.5H5V6H2zM4 7h8l2 6H2z"/></svg>
        +1.555.210.0400 x118
      </li>
      <li class="contact-item">
        <svg class="contact-icon" viewBox="0 0 16 16"><path fill="#08add0" d="M3 1h3l1 4-2 1.5a9 9 0 0 0 4.5 4.5L11 9l4 1v3c0 1-1 2-2 2C7 15 1 9 1 3c0-1 1-2 2-2z"/></svg>
        +1.555.304.781
      </li>
      <li class="contact-item">
        <svg class="contact-icon" viewBox="0 0 16 16"><rect x="1" y="3" width="14" height="10" fill="#08add0"/><path d="M1.5 3.5 8 9l6.5-5.5" stroke="#fff" stroke-width="1.4" fill="none"/></svg>
        info@veldmarksupplies.com
      </li>
      <li class="contact-item">
        <svg class="contact-icon" viewBox="0 0 16 16"><circle cx="8" cy="8" r="7" fill="#08add0"/><path d="M1 8h14M8 1c-3 3-3 11 0 14M8 1c3 3 3 11 0 14" stroke="#fff" stroke-width="1" fill="none"/></svg>
        www.veldmarksupplies.com
      </li>
    </ul>
    <p class="address">48 Ridgeway Plaza Linford, TX 79701 USA</p>
  </section>
</main>
</body>
</html>
```